NCBG website design

We need a page template website design for a cms website. Please see the brief attached for the details.
The client is the National Copperfleece Breeders Guild which is an organisation promoting the Copperfleece Sheep Breed within Australia.
Updates

Project Deadline Extended
Reason: So that my top few designs can make changes and re-submit.

Target Market(s)

See attached brief

```html
<!DOCTYPE html>
<html lang="en">
<head>
<meta charset="utf-8">
<title>National Copperfleece Breeders Guild</title>
<link href="https://fonts.googleapis.com/css2?family=Source+Sans+3:ital,wght@0,400;0,600;0,700;1,400&display=swap" rel="stylesheet">
<style>
:root{
  --green:#135e40;
  --green-light:#4f9a6c;
  --yellow:#f5c52e;
  --red:#c1272d;
  --page:#e8e7e5;
  --ink:#3a3a3a;
  --muted:#555;
  --footer:#1c1c1c;
  --line:#c9c9c9;
}
*{margin:0;padding:0;box-sizing:border-box}
html,body{width:929px;height:1200px;overflow:hidden}
body{position:relative;background:var(--page);font-family:Arial,Helvetica,sans-serif;color:var(--ink)}
.abs{position:absolute}
.site-header{left:0;top:0;width:929px;height:102px;background:#fff}
.brand-mark{left:88px;top:22px;width:56px;height:56px;border:3px solid var(--green);background:var(--yellow);border-radius:6px}
.brand-name{left:155px;top:26px;font-family:"Source Sans 3",sans-serif;font-weight:700;font-size:34px;line-height:40px;color:var(--green);white-space:nowrap;letter-spacing:.3px}
.tagline{right:194px;top:62px;font-family:"Source Sans 3",sans-serif;font-style:italic;font-size:16px;color:var(--red)}
.main-nav{left:0;top:102px;width:929px;height:36px;background:var(--green)}
.main-nav a{position:absolute;top:0;line-height:36px;font-size:10px;font-weight:700;color:#fff;text-decoration:none;transform:translateX(-50%);letter-spacing:.3px}
.main-nav a.active{top:5px;line-height:26px;width:66px;text-align:center;background:#2b2b2b;border:1px solid #555;border-radius:3px}
.hero{left:0;top:138px;width:929px;height:343px;background:linear-gradient(100deg,#8a8176 0%,#c9c3b8 30%,#d8d2c8 45%,#a89f92 65%,#8c7a6c 100%)}
.feature-card{top:428px;width:167px;height:214px;background:linear-gradient(#dcdcdc 0,#f4f4f4 60px,#fff 100%);border-top:7px solid var(--yellow);border-radius:0 0 8px 8px;box-shadow:0 1px 3px rgba(0,0,0,.08);text-align:center}
.feature-card .icon-ring{position:absolute;left:46px;top:34px;width:76px;height:76px;border-radius:50%;background:#fff;border:7px solid #ececec;display:flex;align-items:center;justify-content:center}
.feature-card h3{position:absolute;left:0;right:0;top:132px;font-family:"Source Sans 3",sans-serif;font-weight:700;font-size:14.5px;color:var(--ink)}
.feature-card p{position:absolute;left:0;right:0;top:151px;font-size:13px;color:var(--muted)}
.feature-card .more{position:absolute;left:0;right:0;top:176px;font-size:8.5px;font-style:italic;color:#d9a81c}
.tab{top:669px;height:34px;line-height:33px;font-family:"Source Sans 3",sans-serif;font-weight:600;font-size:14.5px;color:#555;background:linear-gradient(#f2f2f2,#dedede);border:1px solid var(--line);border-bottom:none;padding-left:11px}
.tab.active{background:linear-gradient(var(--green-light),#237a4b);color:#fff;text-align:center;padding-left:0;border-color:#237a4b}
.tab-panel{left:103px;top:702px;width:729px;height:188px;border:1px solid var(--line);border-radius:0 4px 4px 4px;background:linear-gradient(#f2f2f2,#e3e3e3)}
.tab-photo{left:118px;top:727px;width:166px;height:128px;border:5px solid var(--yellow);background:linear-gradient(#5d7a44,#a8a48e 45%,#6f9a48)}
.tab-copy{left:298px;top:729px;width:514px;font-size:9.6px;line-height:15.5px;color:#444}
.tab-copy p+p{margin-top:15px}
.sponsors{left:104px;top:953px;width:730px;height:91px;border:1px solid var(--line)}
.sponsors-title{left:399px;top:928px;width:130px;height:38px;background:var(--page);border:1px solid #fff;outline:1px solid #ddd;text-align:center;line-height:36px;font-family:"Source Sans 3",sans-serif;font-weight:600;font-size:17px;color:var(--green)}
.sponsor{top:988px;font-family:"Source Sans 3",sans-serif;font-weight:600;font-size:12px;line-height:14px;color:#6a6a6a;transform:translateX(-50%);white-space:nowrap}
.site-footer{left:0;top:1069px;width:929px;height:131px;background:var(--footer)}
.footer-links{left:0;right:0;top:1083px;text-align:center;font-family:"Source Sans 3",sans-serif;font-size:9.5px;color:#bbb}
.footer-links span{padding:0 5px}
.footer-links i{font-style:normal;color:#777}
.social-btn{left:388px;top:1120px;width:156px;height:20px;background:#3b5c9e;border:1px solid #6a86c0;color:#fff;font-family:"Source Sans 3",sans-serif;font-weight:700;font-size:11.5px;line-height:18px;padding-left:22px;white-space:nowrap;overflow:hidden}
.social-btn::before{content:"";position:absolute;left:5px;top:3px;width:12px;height:12px;background:#fff;opacity:.9}
.copyright{left:0;right:0;top:1157px;text-align:center;font-size:9.6px;line-height:15px;color:#aaa}
.bottom-strip{left:0;top:1195px;width:929px;height:5px;background:var(--green)}
</style>
</head>
<body>
<header class="site-header abs">
  <div class="brand-mark abs"></div>
  <div class="brand-name abs">National Copperfleece Breeders Guild</div>
  <div class="tagline abs">...Better by Design</div>
</header>
<nav class="main-nav abs">
  <a class="active" style="left:122px">HOME</a>
  <a style="left:223px">ABOUT</a>
  <a style="left:334px">SEARCH</a>
  <a style="left:470px">STUD PAGES</a>
  <a style="left:593px">SALES</a>
  <a style="left:696px">LINKS</a>
  <a style="left:821px">CONTACT</a>
</nav>
<div class="hero abs" role="img" aria-label="Photo of woolly sheep standing in a shearing shed"></div>

<section class="feature-card abs" style="left:107px">
  <div class="icon-ring"><svg width="26" height="26" viewBox="0 0 26 26"><circle cx="13" cy="13" r="10" fill="none" stroke="#135e40" stroke-width="2.5"/><circle cx="13" cy="13" r="3" fill="#135e40"/></svg></div>
  <h3>Prime Lamb Helpline</h3><p>Lorem Ipsum dolor.</p><div class="more">read more</div>
</section>
<section class="feature-card abs" style="left:286px">
  <div class="icon-ring"><svg width="24" height="24" viewBox="0 0 24 24"><rect x="2" y="4" width="20" height="18" fill="#135e40"/><rect x="6" y="1" width="2" height="5" fill="#135e40"/><rect x="16" y="1" width="2" height="5" fill="#135e40"/><g fill="#fff"><rect x="5" y="10" width="3" height="3"/><rect x="10.5" y="10" width="3" height="3"/><rect x="16" y="10" width="3" height="3"/><rect x="5" y="15.5" width="3" height="3"/><rect x="10.5" y="15.5" width="3" height="3"/><rect x="16" y="15.5" width="3" height="3"/></g></svg></div>
  <h3>Events</h3><p>Lorem Ipsum dolor.</p><div class="more">read more</div>
</section>
<section class="feature-card abs" style="left:467px">
  <div class="icon-ring"><svg width="24" height="24" viewBox="0 0 24 24"><circle cx="10" cy="6" r="5" fill="#135e40"/><path d="M2 23c0-7 3-10 8-10s8 3 8 10z" fill="#135e40"/><path d="M19 14v8M15 18h8" stroke="#135e40" stroke-width="2.5"/></svg></div>
  <h3>Members</h3><p>Lorem Ipsum dolor.</p><div class="more">read more</div>
</section>
<section class="feature-card abs" style="left:653px">
  <div class="icon-ring"><svg width="26" height="22" viewBox="0 0 26 22"><rect x="1" y="1" width="24" height="20" fill="none" stroke="#135e40" stroke-width="2.5"/><rect x="5" y="5" width="7" height="6" fill="#135e40"/><path d="M14 6h7M14 10h7M5 15h16" stroke="#135e40" stroke-width="2"/></svg></div>
  <h3>Latest News</h3><p>Lorem Ipsum dolor.</p><div class="more">read more</div>
</section>

<div class="tab active abs" style="left:103px;width:116px">Why Us</div>
<div class="tab abs" style="left:222px;width:134px">Copperfleece</div>
<div class="tab abs" style="left:359px;width:134px">Cross Breed</div>
<div class="tab abs" style="left:496px;width:135px">Progency Testing</div>
<div class="tab-panel abs"></div>
<div class="tab-photo abs" role="img" aria-label="Photo of a sheep standing on green pasture"></div>
<div class="tab-copy abs">
  <p>Lorem ipsum dolor sit amet, consectetur adipiscing elit etiam accumsan, ipsum a tristique varius nec euismod elit massa vitae odio. Vestibulum sodales nisi quis nisi imperdiet scelerisque euismod ulum elit odio, eu porta metus aenean Lorem ipsum dolor sit amet, consectetur adipiscing elit etiam accumsan, ipsum a tristique varius non euismod elit massa vitae odio.</p>
  <p>Vestibulum sodales nisi quis nisi imperdiet scelerisque euismod ulum elit odio, eu porta metus aenean posuere hendrerit lacus sit amet venenatis. posuere hendrerit lacus sit amet venenatis.Lorem ipsum dolor sit amet, consectetur adipiscing elit etiam accumsan.quis nisi imperdiet scelerisque euismod ulum elit odio, eu porta metus aenean posuere</p>
</div>

<div class="sponsors abs"></div>
<div class="sponsors-title abs">Our Sponsors</div>
<span class="sponsor abs" style="left:185px">Ridgeway</span>
<span class="sponsor abs" style="left:270px">Kestrel</span>
<span class="sponsor abs" style="left:348px">Orvane</span>
<span class="sponsor abs" style="left:433px">Basalt</span>
<span class="sponsor abs" style="left:511px">Tarrow</span>
<span class="sponsor abs" style="left:600px">Quarrymark</span>
<span class="sponsor abs" style="left:730px;top:978px">Summitline</span>
<span class="sponsor abs" style="left:706px;top:996px">Ironbark</span>
<span class="sponsor abs" style="left:768px;top:996px">Glenfuel</span>

<footer class="site-footer abs"></footer>
<div class="footer-links abs"><span>Home</span><i>|</i><span>About Us</span><i>|</i><span>Members</span><i>|</i><span>Stud Pages</span><i>|</i><span>News</span><i>|</i><span>Sales</span><i>|</i><span>Link</span><i>|</i><span>Contact</span></div>
<div class="social-btn abs">Connect with Pasturenet</div>
<div class="copyright abs">Copyright © 2014 National Copperfleece Breeders Guild. All rights reserved.<br>Website design and development by Woolgate Studio</div>
<div class="bottom-strip abs"></div>
</body>
</html>
```